New Web Design Project

Number of Pages Required

1 page

Requirements
Must have
• An Overview / Background of the Business & Services(not for profit rescue animal farm)
• The Target Market / Audience you are trying to reach (animal lovers)
• Design Specifics; any preferences or ideas for Style, Colour, Imagery, etc (no preferences)

```html
<!DOCTYPE html>
<html lang="en">
<head>
<meta charset="utf-8">
<title>Cedar Hollow Farms</title>
<link rel="stylesheet" href="https://fonts.googleapis.com/css2?family=Montserrat:wght@400;500;600;700&family=Lato:wght@400;700&display=swap">
<style>
:root{
  --green:#1f8a2c;
  --green-dark:#176b21;
  --ink:#222;
  --text:#444;
  --muted:#666;
  --dark:#2a2a2a;
  --white:#fff;
  --line:#ddd;
}
*{box-sizing:border-box;margin:0;padding:0}
html,body{width:1200px;height:3965px;overflow:hidden;background:var(--white)}
body{position:relative;font-family:'Lato',sans-serif;color:var(--text)}
.abs{position:absolute}
a{color:inherit;text-decoration:none}

/* header */
.site-header{position:absolute;left:0;top:0;width:1200px;height:110px;background:var(--white)}
.brand{left:177px;top:20px;width:95px;height:80px;display:flex;align-items:center;gap:6px;font-family:'Montserrat',sans-serif;font-weight:700;font-size:19px;line-height:1.05;color:var(--green)}
.top-actions{left:793px;top:0;display:flex;height:35px}
.top-actions a{display:flex;align-items:center;justify-content:center;font-family:'Montserrat',sans-serif;font-weight:600;font-size:13px;color:var(--white)}
.btn-login{width:100px;background:var(--dark);clip-path:polygon(12% 0,100% 0,100% 100%,0 100%)}
.btn-donate-top{width:132px;background:var(--green);clip-path:polygon(0 0,100% 0,88% 100%,0 100%)}
.main-nav{left:476px;top:68px;display:flex;gap:0;font-family:'Montserrat',sans-serif;font-weight:600;font-size:14px;color:var(--ink)}
.main-nav a{position:absolute;white-space:nowrap}
.main-nav .active{color:var(--green)}

/* hero */
.hero{left:0;top:110px;width:1200px;height:545px;background:linear-gradient(180deg,#3f6b2a 0%,#5d8f34 45%,#7fb83f 75%,#8cc44a 100%)}
.hero-title{left:0;top:335px;width:1200px;text-align:center;font-family:'Montserrat',sans-serif;font-weight:700;font-size:40px;letter-spacing:3px;color:var(--white)}
.btn-hero{left:523px;top:402px;width:154px;height:36px;background:var(--green);color:var(--white);font-family:'Montserrat',sans-serif;font-weight:600;font-size:15px;display:flex;align-items:center;justify-content:center}
.hero-dots{left:513px;top:598px;display:flex;gap:8px}
.hero-dots span{width:40px;height:4px;background:rgba(255,255,255,.5)}
.hero-dots span.on{background:var(--white)}
.hero-edge{left:0;top:615px;width:1200px;height:45px}

/* section headings */
.section-title{left:0;width:1200px;text-align:center;font-family:'Montserrat',sans-serif;font-weight:500;font-size:34px;color:var(--ink)}

/* service cards */
.card{width:267px}
.card-media{height:180px;position:relative}
.card-tag{position:absolute;left:0;top:12px;background:rgba(60,60,60,.8);color:var(--white);font-size:13px;padding:5px 10px;font-family:'Lato',sans-serif}
.card-text{margin-top:17px;font-size:11.5px;line-height:19px;color:var(--text)}
.btn-outline{display:inline-flex;align-items:center;justify-content:center;margin-top:18px;width:97px;height:32px;border:2px solid var(--green);color:var(--ink);font-family:'Montserrat',sans-serif;font-weight:600;font-size:13px}

/* videos */
.herd-strip{left:0;top:1510px;width:1200px;height:76px;background:linear-gradient(180deg,#fff 0%,#e7e4de 100%)}
.videos-light{left:0;top:1586px;width:1200px;height:357px;background:linear-gradient(180deg,#e9e6e0,#d9d5cc)}
.videos-dark{left:0;top:1943px;width:1200px;height:594px;background:linear-gradient(180deg,#4a4a40 0%,#2f2f2a 60%,#3a3a30 100%)}
.video-frame{left:174px;top:1728px;width:853px;height:450px;background:linear-gradient(180deg,#5b6b4a 0%,#6e8f45 50%,#5c8a36 100%)}
.play{left:570px;top:1923px;width:60px;height:60px;border-radius:50%;background:rgba(20,20,20,.75)}
.why-title{color:var(--white)}
.feature{width:283px;text-align:center;color:var(--white);font-family:'Montserrat',sans-serif;font-size:17px;line-height:26px}
.feature svg{display:block;margin:0 auto 18px}
.divider{width:1px;height:110px;background:rgba(255,255,255,.6)}

/* events */
.events-intro{left:300px;top:2668px;width:600px;text-align:center;font-size:13px;line-height:22px;color:var(--text)}
.event-feature{left:174px;top:2746px;width:476px;height:301px;background:linear-gradient(180deg,#c98a3c 0%,#8c7a55 45%,#6d7a4a 100%)}
.event-card{left:190px;top:2902px;width:460px;height:164px;background:var(--white);box-shadow:0 2px 10px rgba(0,0,0,.15);padding:32px 22px 0 26px}
.date{display:inline-block;background:var(--green);color:var(--white);font-size:11px;font-weight:700;padding:3px 8px;border-radius:2px}
.event-card .date{position:absolute;left:26px;top:14px}
.event-title{font-family:'Montserrat',sans-serif;font-weight:600;font-size:17px;color:var(--ink)}
.event-text{font-size:11.5px;line-height:19px;color:var(--text);margin-top:8px}
.read-link{display:block;margin-top:10px;font-family:'Montserrat',sans-serif;font-weight:600;font-size:11px;color:var(--green)}
.pager{left:592px;top:2938px;display:flex;flex-direction:column;gap:8px}
.pager span{width:30px;height:30px;display:flex;align-items:center;justify-content:center;color:var(--white);background:#444}
.pager span.off{background:#ddd}
.event-thumb{width:158px;height:148px}
.event-side{width:185px}
.event-side .date{margin-bottom:10px}

/* testimonial */
.testimonial{left:0;top:3180px;width:1200px;height:407px;background:linear-gradient(180deg,#d9dbc9 0%,#b9c2a0 60%,#9aa77c 100%)}
.quote-mark{left:0;top:3268px;width:1200px;text-align:center;font-family:'Montserrat',sans-serif;font-weight:700;font-size:70px;line-height:60px;color:var(--green)}
.quote-text{left:345px;top:3336px;width:510px;text-align:center;font-style:italic;font-size:14px;line-height:27px;color:#333}
.quote-name{left:0;top:3500px;width:1200px;text-align:center;font-family:'Montserrat',sans-serif;font-weight:600;font-size:13px;color:var(--green)}

/* footer */
.footer-col h4{font-family:'Montserrat',sans-serif;font-weight:600;font-size:16px;color:var(--ink);margin-bottom:20px}
.footer-col p{font-size:11.5px;line-height:21px;color:var(--text)}
.footer-col ul{list-style:none}
.footer-col li{font-size:12px;line-height:22.5px;color:var(--text)}
.socials{display:flex;gap:12px}
.socials span{width:12px;height:12px;border-radius:50%;background:var(--ink)}
.footer-sheep{left:925px;top:3727px;width:211px;height:238px;background:linear-gradient(180deg,#e9e2d2,#cdbfa4);border-radius:90px 90px 0 0}
.footer-rule{left:174px;top:3877px;width:720px;height:1px;background:var(--line)}
.copyright{left:174px;top:3906px;width:720px;text-align:center;font-size:13px;color:var(--text)}
</style>
</head>
<body>

<header class="site-header">
  <div class="abs brand"><span>CEDAR<br>HOLLOW</span></div>
  <div class="abs top-actions">
    <a class="btn-login" href="#">Log In</a>
    <a class="btn-donate-top" href="#">Donate Here</a>
  </div>
  <nav class="abs main-nav">
    <a class="active" style="left:0">Home</a>
    <a style="left:69px">Our Farm</a>
    <a style="left:161px">Sponsorship</a>
    <a style="left:275px">Events</a>
    <a style="left:349px">Customer Reviews</a>
    <a style="left:510px">Contact</a>
  </nav>
</header>

<section>
  <div class="abs hero" role="img" aria-label="Sheep grazing on green grass in a forest clearing"></div>
  <h1 class="abs hero-title">CEDAR HOLLOW FARMS</h1>
  <a class="abs btn-hero" href="#">Donate Now</a>
  <div class="abs hero-dots"><span class="on"></span><span></span><span></span></div>
  <svg class="abs hero-edge" viewBox="0 0 1200 45" preserveAspectRatio="none"><path d="M0 28 Q80 18 160 30 T320 26 T480 32 T640 24 T800 30 T960 26 T1120 32 L1200 22 L1200 45 L0 45Z" fill="#fff"/></svg>
</section>

<section>
  <h2 class="abs section-title" style="top:714px">Welcome to Cedar Hollow Farms</h2>

  <article class="abs card" style="left:174px;top:803px">
    <div class="card-media" role="img" aria-label="Rescued sheep gathered in a pen" style="background:linear-gradient(180deg,#b6b1a6,#8c8374)"><span class="card-tag">Rescue</span></div>
    <p class="card-text">Sed ut perspiciatis unde omnis iste natus err voluptatem accu torsantium doloremque laudan tium, totam rem aperiam, eaque ipsa.</p>
    <a class="btn-outline" href="#">Read More</a>
  </article>
  <article class="abs card" style="left:465px;top:803px">
    <div class="card-media" role="img" aria-label="Volunteer with a white goat in a field" style="background:linear-gradient(180deg,#7e9a62,#5e7a45)"><span class="card-tag">Educate</span></div>
    <p class="card-text">Sed ut perspiciatis unde omnis iste natus err voluptatem accu torsantium doloremque laudan tium, totam rem aperiam, eaque ipsa.</p>
    <a class="btn-outline" href="#">Read More</a>
  </article>
  <article class="abs card" style="left:758px;top:803px">
    <div class="card-media" role="img" aria-label="Brown and white goats in a barn" style="background:linear-gradient(180deg,#6a4a36,#3f2b20)"><span class="card-tag">Donate</span></div>
    <p class="card-text">Sed ut perspiciatis unde omnis iste natus err voluptatem accu torsantium doloremque laudan tium, totam rem aperiam, eaque ipsa.</p>
    <a class="btn-outline" href="#">Read More</a>
  </article>

  <article class="abs card" style="left:174px;top:1147px">
    <div class="card-media" role="img" aria-label="Brown hens feeding together" style="background:linear-gradient(180deg,#b5642e,#7c3d1a)"><span class="card-tag">Support Us</span></div>
    <p class="card-text">Sed ut perspiciatis unde omnis iste natus err voluptatem accu torsantium doloremque laudan tium, totam rem aperiam, eaque ipsa.</p>
    <a class="btn-outline" href="#">Read More</a>
  </article>
  <article class="abs card" style="left:465px;top:1147px">
    <div class="card-media" role="img" aria-label="Farm family standing in a sunny meadow" style="background:linear-gradient(180deg,#a7b46a,#5f7a34)"><span class="card-tag">Meet our Residents</span></div>
    <p class="card-text">Sed ut perspiciatis unde omnis iste natus err voluptatem accu torsantium doloremque laudan tium, totam rem aperiam, eaque ipsa.</p>
    <a class="btn-outline" href="#">Read More</a>
  </article>
  <article class="abs card" style="left:758px;top:1147px">
    <div class="card-media" role="img" aria-label="Visitors meeting horses at a paddock" style="background:linear-gradient(180deg,#8a8c7a,#4e5040)"><span class="card-tag">Visit or Volunteer</span></div>
    <p class="card-text">Sed ut perspiciatis unde omnis iste natus err voluptatem accu torsantium doloremque laudan tium, totam rem aperiam, eaque ipsa.</p>
    <a class="btn-outline" href="#">Read More</a>
  </article>
</section>

<section>
  <div class="abs herd-strip" role="img" aria-label="Faint band of farm animal silhouettes"></div>
  <div class="abs videos-light" role="img" aria-label="Cattle grazing in a soft faded field"></div>
  <div class="abs videos-dark" role="img" aria-label="Herd of cows at dusk on a dark pasture"></div>
  <h2 class="abs section-title" style="top:1638px">Our Videos</h2>
  <div class="abs video-frame" role="img" aria-label="Video still of sheep grazing with birds in a green meadow"></div>
  <div class="abs play"><svg width="60" height="60" viewBox="0 0 60 60"><path d="M24 18 L42 30 L24 42Z" fill="#fff"/></svg></div>

  <h2 class="abs section-title why-title" style="top:2217px">Why Choose Cedar Hollow Farms</h2>
  <div class="abs feature" style="left:183px;top:2292px">
    <svg width="70" height="78" viewBox="0 0 70 78" fill="none" stroke="#fff" stroke-width="2.5"><path d="M35 4 L64 14 V38 C64 56 50 68 35 74 C20 68 6 56 6 38 V14Z"/><circle cx="35" cy="38" r="16"/><path d="M28 45 L42 31"/><circle cx="29" cy="32" r="2"/><circle cx="41" cy="44" r="2"/></svg>
    Lorem ipsum<br>dolormeorem ipsum<br>dolormevolvo
  </div>
  <div class="abs divider" style="left:457px;top:2300px"></div>
  <div class="abs feature" style="left:458px;top:2292px">
    <svg width="70" height="78" viewBox="0 0 70 78" fill="none" stroke="#fff" stroke-width="2.5"><rect x="14" y="4" width="42" height="56" rx="3"/><path d="M22 16 H48 M22 24 H48 M22 32 H40"/><circle cx="35" cy="50" r="8"/><path d="M30 57 L27 74 L35 69 L43 74 L40 57"/></svg>
    Lorem ipsum<br>dolormeorem ipsum<br>dolormevolvo
  </div>
  <div class="abs divider" style="left:740px;top:2300px"></div>
  <div class="abs feature" style="left:741px;top:2292px">
    <svg width="70" height="78" viewBox="0 0 70 78" fill="none" stroke="#fff" stroke-width="2.5"><circle cx="30" cy="34" r="12"/><path d="M8 72 C10 56 20 50 30 50 C40 50 50 56 52 72Z"/><rect x="40" y="4" width="26" height="26" rx="3"/><path d="M53 10 L55.5 15 L61 15.5 L57 19 L58 24 L53 21.5 L48 24 L49 19 L45 15.5 L50.5 15Z"/></svg>
    Lorem ipsum<br>dolormeorem ipsum<br>dolormevolvo
  </div>
</section>

<section>
  <h2 class="abs section-title" style="top:2618px">Farm Events</h2>
  <p class="abs events-intro">Serror sit voluptatem accusantium doloremque laudanti um, totam rem aperiam, eaque ipsa quae ab illo et quasi archite cto beatSerror sit voluptatem accusantium doloremque laudanti um, totam.</p>

  <div class="abs event-feature" role="img" aria-label="Flock of sheep in a field at golden sunset"></div>
  <article class="abs event-card">
    <span class="date">Feb 11 2019</span>
    <h3 class="event-title">Lorem ipsum dolormevol</h3>
    <p class="event-text">Serror sit voluptatem accusantium doloremque laudanti um,<br>totam rem aperiam, eaque ipsa quae ab illoquasi archite.</p>
    <a class="read-link" href="#">READ MORE</a>
  </article>
  <div class="abs pager"><span>›</span><span class="off">‹</span></div>

  <div class="abs event-thumb" style="left:669px;top:2746px;background:linear-gradient(180deg,#8a9a5a,#7a4a2a)" role="img" aria-label="Hens in a grassy yard"></div>
  <article class="abs event-side" style="left:843px;top:2746px">
    <span class="date">Feb 11 2019</span>
    <h3 class="event-title" style="font-size:16px">Lorem ipsum dolorme</h3>
    <p class="event-text">Serror sit voluptatem accusantium doloremque laudanti uota.</p>
    <a class="read-link" href="#">READ MORE</a>
  </article>
  <div class="abs event-thumb" style="left:669px;top:2918px;background:linear-gradient(180deg,#5a4030,#2e2420)" role="img" aria-label="Cows in a barn stall"></div>
  <article class="abs event-side" style="left:843px;top:2918px">
    <span class="date">Feb 11 2019</span>
    <h3 class="event-title" style="font-size:16px">Lorem ipsum dolorme</h3>
    <p class="event-text">Serror sit voluptatem accusantium doloremque laudanti uota.</p>
    <a class="read-link" href="#">READ MORE</a>
  </article>
</section>

<section>
  <div class="abs testimonial" role="img" aria-label="Sheep grazing under misty pine trees"></div>
  <div class="abs quote-mark">“</div>
  <p class="abs quote-text">Sed ut perspiciatis unde omnis iste natus error voluptatem accu torsantium doloremque laudan tium, totam rem aperiam, eaque ipsaed ut pfre erspiciatis unde omnis iste natus err voluptatemaccu doloremque laudan tium, totam rem aperiam, eaque ipsaed ut pfre erspiciatis undeomis iste natus err voluptate accu lorea.</p>
  <p class="abs quote-name">ARUN VALE</p>
</section>

<footer>
  <div class="abs footer-col" style="left:174px;top:3664px;width:300px">
    <h4>About Us</h4>
    <p>Serror sit voluptatem accusantium doloremque laudant ium, otam rem aperiam, eaque ipsa quae ab illoquasi arc hite.Serror sit voluptatem accusantium doloremque la udanti um, totam rem aperiam, eaque ipsa quae ab illoqu asi archite.Serror sit voluptatem accusantium doloremue laudanti um,totam rem aperiam, eaq</p>
  </div>
  <div class="abs footer-col" style="left:539px;top:3664px">
    <h4>Links</h4>
    <ul><li>Home</li><li>Our Farm</li><li>How it Works</li><li>Events</li><li>Customer Reviews</li><li>FAQ</li></ul>
  </div>
  <div class="abs footer-col" style="left:735px;top:3664px">
    <h4>Our Service</h4>
    <ul><li>Donation</li><li>Sponsor an Animal</li><li>Loremipsum</li><li>Our Partners</li><li>Volunteer</li></ul>
  </div>
  <div class="abs footer-col" style="left:928px;top:3664px">
    <h4>Follow us on</h4>
    <div class="socials"><span></span><span></span><span></span><span></span></div>
  </div>
  <div class="abs footer-sheep" role="img" aria-label="White sheep looking toward the viewer"></div>
  <div class="abs footer-rule"></div>
  <p class="abs copyright">Copyrights © 2019 Cedar Hollow Farms. All Rights Reserved.</p>
</footer>

</body>
</html>
```